Website design needed for gift based dropship website

I am building a dropshipping website that will create gift based merchandise and send it out to our clients customers for them. Our clients will sell products and when a customer buys from them, we create the item and send it out to the customer.

I am looking for a very similar website to stitchora.com - that website is doing a very similar thing to what i am doing but where the stitchora website is based around clothing, my website will be based around gifts. Another website that i like that is doing a similar thing to what i will do is pelvane.com

I require 2 pages to be made:
1) The home page
2) A landing page for a free product giveaway offer

1) THE HOME PAGE
The home page should be a merger of the two previously stated websites (www.pelvane.com and www.stitchora.com). The style fo the homepage should be based on the logo that is attached and the colour scheme should be similar but basic.

2) THE LANDING PAGE
The landing page will be giving away a free mobile phone cover. The page needs to have some mobile phone covers for different phones all with random designs on. The page should state that they can have any design that they want and they do not pay for the phone (they only pay for shipping).

Menu pages and text should be taken from the stitchora.com website.

Target Market(s)

18 - 40 year old males. People who like the idea of earning extra money in their spare time but aren't too sure how to do it. Semi-professional jobs.

Font styles to use
Serif
Sans Serif
Decorative
Script

Colors

Designer to choose colors to be used in the design.

Requirements
Must have
• A "how it works" image where the dropshipping process is explained to a visitor to the website (similar to the one on the stitchora "how it works page")
Nice to have
• Testimonial area on homepage
Should not have
• Homepage should not have:
• - "latest orders from" area
• - Video
• - Warehousing/fulfilment area
• - Integration area

```html
<!DOCTYPE html>
<html lang="en">
<head>
<meta charset="utf-8">
<title>Hollowmere — Gift Dropshipping</title>
<link href="https://fonts.googleapis.com/css2?family=Roboto+Condensed:wght@400;700&family=Questrial&family=Montserrat:wght@400;600;700&display=swap" rel="stylesheet">
<style>
:root{
  --red:#e8493a;
  --red-deep:#e3342a;
  --rose:rgba(246,160,150,.72);
  --maroon:#5a1f2a;
  --ink:#1d1d1f;
  --text:#555;
  --muted:#8a8a8a;
  --yellow:#eab514;
  --cyan:#3bbde0;
  --pink:#ee99c0;
  --black:#0e0e0e;
  --white:#fff;
  --card:#f4f4f4;
  --line:#e3e3e3;
  --head:"Roboto Condensed",sans-serif;
  --body:"Questrial",sans-serif;
  --label:"Montserrat",sans-serif;
}
*{box-sizing:border-box;margin:0;padding:0}
html,body{width:1200px;height:3000px;overflow:hidden;background:var(--white)}
body{position:relative;font-family:var(--body);color:var(--text)}
.abs{position:absolute}

/* hero */
.hero-photo{left:0;top:0;width:600px;height:632px;background:linear-gradient(90deg,#d9d7d6 0%,#d0cdcc 30%,#c96a5e 45%,#b8463c 58%,#cfcccb 75%,#b9b6b5 100%)}
.hero-red{left:600px;top:0;width:600px;height:632px;background:var(--red)}
.brand{left:0;top:0;width:250px;height:96px;background:var(--white);display:flex;align-items:center;gap:10px;padding-left:40px}
.brand-dot{width:16px;height:16px;border-radius:50%;background:var(--red-deep)}
.brand-name{font-family:var(--body);font-size:24px;line-height:1;color:var(--ink)}
.search{left:1082px;top:20px}
.menu-btn{left:1134px;top:0;width:66px;height:64px;background:var(--white);display:flex;flex-direction:column;justify-content:center;align-items:center;gap:5px}
.menu-btn span{width:22px;height:3px;background:#3c5ca8}
.hero-panel{left:500px;top:216px;width:512px;height:202px;background:var(--rose);border:3px solid var(--white)}
.hero-tag{left:520px;top:372px;transform:rotate(-90deg);transform-origin:left top;font-family:var(--label);font-weight:700;font-size:10px;line-height:14px;color:var(--red-deep);text-transform:uppercase;letter-spacing:.5px;width:140px}
.hero-title{left:656px;top:250px;font-family:var(--label);font-weight:600;font-size:35px;color:var(--white);letter-spacing:.5px}
.hero-sub{left:656px;top:302px;width:240px;font-size:12px;line-height:17px;color:var(--white)}
.btn-white{left:656px;top:350px;width:130px;height:36px;background:var(--white);color:var(--ink);font-family:var(--label);font-size:11px;font-weight:600;display:flex;align-items:center;justify-content:center}
.mouse{left:616px;top:566px}

/* how it works */
.section-title{font-family:var(--head);font-weight:700;font-size:38px;color:var(--ink);text-transform:uppercase}
.how-title{left:0;top:710px;width:1200px;text-align:center}
.step{top:816px;width:192px;height:206px;border:3px dashed var(--maroon);text-align:center;padding-top:38px}
.step h3{font-family:var(--label);font-weight:600;font-size:19px;line-height:22px;color:var(--ink)}
.step p{font-size:12px;line-height:20px;color:var(--ink);margin:12px auto 0;width:140px}
.step .pill{position:absolute;left:34px;bottom:34px;width:120px;height:30px;font-family:var(--label);font-size:11px;font-weight:600;color:var(--white);display:flex;align-items:center;justify-content:center}

/* products */
.products-title{left:48px;top:1172px}
.products-lead{left:48px;top:1252px;font-family:var(--label);font-weight:600;font-size:12px;color:var(--ink)}
.products-copy{left:48px;top:1282px;width:330px;font-size:11.5px;line-height:17px;color:var(--muted)}
.products-copy p+p{margin-top:14px}
.read-more{font-family:var(--label);font-size:11px;font-weight:600;color:var(--ink);display:flex;align-items:center;gap:8px}
.products-more{left:48px;top:1446px}
.tile{overflow:hidden}
.tile-a{left:422px;top:1150px;width:244px;height:172px;background:linear-gradient(135deg,#f2f2f2,#d86a5e 55%,#3a6fb8)}
.tile-b{left:666px;top:1150px;width:214px;height:342px;background:linear-gradient(180deg,#e3e3e3,#7c7c7c 60%,#3e3e3e)}
.tile-c{left:880px;top:1150px;width:320px;height:172px;background:var(--yellow);padding:48px 28px 0 30px;color:var(--white)}
.tile-c h4{font-family:var(--label);font-weight:600;font-size:11px;line-height:16px}
.tile-c p{font-size:10.5px;margin-top:10px}
.tile-c .read-more{color:var(--white);margin-top:16px;font-size:10px}
.tile-d{left:422px;top:1322px;width:244px;height:170px;background:linear-gradient(135deg,#5dc4c0,#e4b03c 55%,#d6393a)}
.tile-e{left:880px;top:1322px;width:320px;height:170px;background:linear-gradient(180deg,#e9e1da,#d9a58b 60%,#c74037)}

/* different */
.diff-red{left:0;top:1582px;width:600px;height:530px;background:var(--red)}
.diff-black{left:600px;top:1582px;width:600px;height:530px;background:var(--black)}
.diff-panel{left:160px;top:1664px;width:482px;height:368px;background:var(--rose);border:3px solid var(--white)}
.diff-title{left:230px;top:1738px;font-family:var(--label);font-weight:600;font-size:22px;color:var(--white);text-transform:uppercase}
.diff-item{left:234px;width:350px;color:var(--white)}
.diff-item h4{font-family:var(--label);font-weight:600;font-size:13px}
.diff-item p{font-size:11px;line-height:17px;margin-top:12px;width:300px}
.diff-more{left:234px;top:1980px}
.diff-more.read-more{color:var(--white)}
.signup-title{left:732px;top:1696px;font-family:var(--label);font-weight:600;font-size:27px;line-height:34px;color:var(--white);text-transform:uppercase}
.signup-title em{font-style:normal;color:var(--red-deep)}
.field{left:732px;width:308px;height:30px;border:1px solid #bfbfbf;font-size:11px;color:#c9c9c9;padding:8px 10px}
.btn-red{left:732px;top:1950px;width:92px;height:30px;background:var(--red-deep);color:var(--white);font-family:var(--label);font-size:11px;font-weight:600;display:flex;align-items:center;justify-content:center}

/* testimonials */
.testi-title{left:190px;top:2238px;font-family:var(--label);font-weight:600;font-size:17px;color:var(--ink);text-transform:uppercase}
.meta{font-family:var(--label);font-size:10px;color:var(--ink);display:flex;gap:20px}
.rule{width:16px;height:2px;background:var(--maroon)}
.testi-meta{left:190px;top:2298px}
.testi-rule{left:190px;top:2328px}
.testi-head{left:190px;top:2350px;font-family:var(--label);font-size:10.5px;font-weight:600;color:var(--ink)}
.testi-copy{left:190px;top:2374px;width:340px;font-size:11px;line-height:16px;color:var(--muted)}
.testi-photo{left:612px;top:2204px;width:400px;height:232px;background:linear-gradient(135deg,#c9d0da,#e0a07a 55%,#efe7e4)}
.testi-more{left:622px;top:2410px;background:var(--white);padding:4px 10px}
.card{top:2502px;width:258px;height:120px;background:var(--card);padding:28px 30px 0}
.card .rule{margin:10px 0 20px}
.card h5{font-family:var(--label);font-weight:600;font-size:10px;color:var(--ink);text-transform:uppercase}
.card.featured{background:var(--yellow)}
.card.featured .meta,.card.featured h5{color:var(--white)}
.card.featured .rule{background:var(--white)}

/* footer */
.foot-line{left:160px;top:2708px;width:880px;height:1px;background:var(--line)}
.foot-nav{left:0;top:2760px;width:1200px;display:flex;justify-content:center;gap:8px}
.foot-nav span{border:1px solid #cfcfcf;padding:6px 12px;font-size:10.5px;color:var(--muted)}
.contact{top:2828px;width:330px}
.contact .row{display:flex;gap:12px;font-size:11px;line-height:17px;color:var(--muted)}
.contact .row+.row{margin-top:22px;align-items:center;color:var(--ink)}
.copyright{left:0;top:2956px;width:1200px;text-align:center;font-size:10.5px;color:var(--muted)}
</style>
</head>
<body>

<!-- hero -->
<div class="abs hero-photo" role="img" aria-label="Smiling woman in a red winter sweater holding a wrapped gift box"></div>
<div class="abs hero-red"></div>
<div class="abs brand"><span class="brand-dot"></span><span class="brand-name">Hollowmere</span></div>
<svg class="abs search" width="22" height="22" viewBox="0 0 22 22"><circle cx="9" cy="9" r="6" fill="none" stroke="#fff" stroke-width="2.2"/><line x1="13.5" y1="13.5" x2="19" y2="19" stroke="#fff" stroke-width="2.4"/></svg>
<div class="abs menu-btn"><span></span><span></span><span></span></div>
<div class="abs hero-panel"></div>
<div class="abs hero-tag">Welcome to the<br>Hollowmere</div>
<div class="abs hero-title">SELL GIFT ONLINE</div>
<div class="abs hero-sub">If you want to sell your designs in an online store or marketplace</div>
<div class="abs btn-white">Connect Your Shop</div>
<svg class="abs mouse" width="28" height="42" viewBox="0 0 28 42"><rect x="2" y="2" width="24" height="38" rx="12" fill="none" stroke="#fff" stroke-width="2"/><line x1="14" y1="10" x2="14" y2="17" stroke="#fff" stroke-width="2"/></svg>

<!-- how it works -->
<h2 class="abs section-title how-title">How It Works</h2>
<div class="abs step" style="left:162px"><h3>Gerry</h3><p>Garry Buys Something At our Store</p><span class="pill" style="background:var(--yellow)">Step One</span></div>
<div class="abs step" style="left:390px"><h3>Your Store</h3><p>Order Get Sent Automatically To Hollowmere</p><span class="pill" style="background:var(--cyan)">Step Two</span></div>
<div class="abs step" style="left:618px"><h3>Hollowmere</h3><p>Product Get Made</p><span class="pill" style="background:var(--pink)">Step Three</span></div>
<div class="abs step" style="left:846px"><h3>Your Product Factory</h3><p>Your Brands All Over It</p><span class="pill" style="background:var(--red-deep)">Step Four</span></div>

<!-- products -->
<h2 class="abs section-title products-title">Our Products</h2>
<div class="abs products-lead">Printed and shipped on demand, under your brand!</div>
<div class="abs products-copy">
  <p>Lorem ipsum dolor sit amet, consectetur adipiscing elit, sed do eiusmod tempor incididunt ut labore et dolore magna aliqua. Ut enim ad minim veniam, quis nostrud exercitation ullamco laboris nisi ut aliquip ex ea commodo consequat.</p>
  <p>Duis aute irure dolor in reprehenderit in voluptate velit esse cillum dolore eu fugiat nulla pariatur. Excepteur sint occaecat cupidatat non proident, sunt in culpa qui officia deserunt mollit anim id est laborum.</p>
</div>
<div class="abs read-more products-more"><svg width="14" height="8" viewBox="0 0 14 8"><path d="M0 4h12M9 1l3 3-3 3" fill="none" stroke="currentColor" stroke-width="1.4"/></svg>Read More</div>
<div class="abs tile tile-a" role="img" aria-label="Stack of colourful wrapped gift boxes"></div>
<div class="abs tile tile-b" role="img" aria-label="Boy in sunglasses wearing a printed T-shirt"></div>
<div class="abs tile tile-c">
  <h4>Lorem ipsum dolor sit amet, consectetur adipiscing elit, sed do eiusmod tempor</h4>
  <p>Lorem ipsum dolor sit amet, consectetur adipiscing elit...</p>
  <div class="read-more"><svg width="14" height="8" viewBox="0 0 14 8"><path d="M0 4h12M9 1l3 3-3 3" fill="none" stroke="currentColor" stroke-width="1.4"/></svg>Read More</div>
</div>
<div class="abs tile tile-d" role="img" aria-label="Hands exchanging a gift box with a red ribbon"></div>
<div class="abs tile tile-e" role="img" aria-label="Open hands holding a small white gift box"></div>

<!-- what makes us different -->
<div class="abs diff-red"></div>
<div class="abs diff-black" role="img" aria-label="Dark textured background"></div>
<div class="abs diff-panel"></div>
<div class="abs diff-title">What Makes Us Different</div>
<div class="abs diff-item" style="top:1798px"><h4>Three fulfillment locations</h4><p>We're located on both sides of the big pond to bring you closer to your customers</p></div>
<div class="abs diff-item" style="top:1894px"><h4>No minimums</h4><p>We print everything on demand so you can order as much as you need and you don't have to keep an inventory</p></div>
<div class="abs read-more diff-more">Read More <svg width="14" height="8" viewBox="0 0 14 8"><path d="M0 4h12M9 1l3 3-3 3" fill="none" stroke="currentColor" stroke-width="1.4"/></svg></div>
<div class="abs signup-title">Create Your<br>Hollowmere<br>Account for <em>Free</em></div>
<div class="abs field" style="top:1826px">Name</div>
<div class="abs field" style="top:1866px">Email</div>
<div class="abs field" style="top:1906px">Password</div>
<div class="abs btn-red">Sign Up</div>

<!-- testimonials -->
<div class="abs testi-title">Testimonials</div>
<div class="abs meta testi-meta"><span>Monday, Jun 4, 2018</span><span>John Smith</span></div>
<div class="abs rule testi-rule"></div>
<div class="abs testi-head">LOREM IPSUM DOLOR SIT AMET CONSECTETOR</div>
<div class="abs testi-copy">Lorem ipsum dolor sit amet, consectetur adipiscing elit, sed do eiusmod tempor incididunt ut labore et dolore magna aliqua. Ut enim ad minim veniam, quis nostrud exercitation ullamco laboris</div>
<div class="abs testi-photo" role="img" aria-label="Red-haired woman opening a gift box"></div>
<div class="abs read-more testi-more"><svg width="14" height="8" viewBox="0 0 14 8"><path d="M0 4h12M9 1l3 3-3 3" fill="none" stroke="currentColor" stroke-width="1.4"/></svg>Read More</div>
<div class="abs card" style="left:188px"><div class="meta"><span>Monday, Jun 4, 2018</span><span>John Smith</span></div><div class="rule"></div><h5>Dolor sit amet consecte</h5></div>
<div class="abs card featured" style="left:470px"><div class="meta"><span>Monday, Jun 4, 2018</span><span>John Smith</span></div><div class="rule"></div><h5>Contetor lorem sit amet</h5></div>
<div class="abs card" style="left:754px"><div class="meta"><span>Monday, Jun 4, 2018</span><span>John Smith</span></div><div class="rule"></div><h5>Lorem ipsum dolor sit amet</h5></div>

<!-- footer -->
<div class="abs foot-line"></div>
<nav class="abs foot-nav"><span>Products &amp; Pricing</span><span>How it Works</span><span>Mockup generator</span><span>Shipping</span><span>Resources</span><span>FAQ</span><span>Blogs</span></nav>
<div class="abs contact" style="left:244px">
  <div class="row"><svg width="14" height="18" viewBox="0 0 14 18"><path d="M7 1a6 6 0 0 0-6 6c0 4.5 6 10 6 10s6-5.5 6-10a6 6 0 0 0-6-6z" fill="var(--yellow)"/><circle cx="7" cy="7" r="2.2" fill="#fff"/></svg><span>Lorem ipsum dolor sit amet, consectetur adipiscing elit, sed do eiusmod tempor incididunt ut labore et dolore magna aliqua.</span></div>
  <div class="row"><svg width="14" height="14" viewBox="0 0 14 14"><path d="M3 1l2.5 3-1.5 1.5a8 8 0 0 0 4.5 4.5L10 8.5l3 2.5-1.5 2C6 13 1 8 1 2.5z" fill="#888"/></svg><span>01 23 456 789</span></div>
</div>
<div class="abs contact" style="left:650px">
  <div class="row"><svg width="14" height="18" viewBox="0 0 14 18"><path d="M7 1a6 6 0 0 0-6 6c0 4.5 6 10 6 10s6-5.5 6-10a6 6 0 0 0-6-6z" fill="var(--yellow)"/><circle cx="7" cy="7" r="2.2" fill="#fff"/></svg><span>Lorem ipsum dolor sit amet, consectetur adipiscing elit, sed do eiusmod tempor incididunt ut labore et dolore magna aliqua.</span></div>
  <div class="row"><svg width="14" height="14" viewBox="0 0 14 14"><path d="M3 1l2.5 3-1.5 1.5a8 8 0 0 0 4.5 4.5L10 8.5l3 2.5-1.5 2C6 13 1 8 1 2.5z" fill="#888"/></svg><span>01 23 456 789</span></div>
</div>
<div class="abs copyright">© Copyright 2018 Hollowmere, all rights Reserved.</div>

</body>
</html>
```